Business Card Design

I am an Event and Wedding Planner in need of an eye catching business card featuring my logo (attached), my contact details, and my company tagline (Making every celebration glow with wonder...) I would like the tagline in font similar the logo's font.
Updates
I have just noticed that my logo has a misspelling so for the final design, I will be uploading a corrected logo as soon as I have it.
My apologies.
Reason: Waiting on a corrected logo...Lantern is misspelled and it should say Weddings not Wedding
The logo has been corrected so now Lantern is spelled correctly and it says Weddings instead of Wedding. Please use Edwardian Script ITC as the font for the tagline so it will match the logo. Thank you for your patience.
Target Market(s)
Engaged couples and people hosting milestone celebrations. 25-50 years old, predominately female
Industry/Entity Type
Business
Contact Information for Business Card
Rosalind Merrow, Event Manager / Owner, Mobile: 0491 868 254, Email: rosalind@velvetlanternco.com.au, www.velvetlanternco.com.au, Making every celebration glow with wonder...

```html
<!DOCTYPE html>
<html lang="en">
<head>
<meta charset="utf-8">
<title>Velvet Lantern – Business Card</title>
<link href="https://fonts.googleapis.com/css2?family=Cormorant+Garamond:wght@400;500&family=Pinyon+Script&display=swap" rel="stylesheet">
<style>
  :root {
    --canvas: #2a2829;
    --blush: #f1cfcd;
    --rose-red: #c4202c;
    --ink: #3a2f2f;
    --slate: #6e6c6d;
    --slate-deep: #5c5a5b;
    --white: #ffffff;
    --photo-light: #eeece7;
    --photo-mid: #e2ddd6;
    --photo-warm: #d6c4bf;
  }
  * { margin: 0; padding: 0; box-sizing: border-box; }
  html, body { width: 1200px; height: 900px; overflow: hidden; }
  body {
    background: var(--canvas);
    font-family: "Cormorant Garamond", Georgia, serif;
    position: relative;
  }
  .card {
    position: absolute;
    left: 260px;
    width: 680px;
    height: 389px;
    overflow: hidden;
    box-shadow: 0 10px 30px rgba(0,0,0,.45);
  }
  .card--front { top: 40px; background: var(--blush); }
  .card--back { top: 471px; background: var(--slate); }

  /* front */
  .bouquet-photo {
    position: absolute; left: 0; top: 0; width: 270px; height: 100%;
    background: linear-gradient(165deg, var(--photo-light) 0%, var(--photo-mid) 55%, var(--photo-warm) 100%);
  }
  .tagline {
    position: absolute; left: 18px; top: 14px; width: 240px;
    font-family: "Pinyon Script", cursive;
    font-size: 19px; line-height: 1.2; color: var(--ink);
  }
  .front-info {
    position: absolute; left: 270px; top: 0; right: 0; bottom: 0;
    text-align: center; color: var(--rose-red);
  }
  .brand-name {
    margin-top: 70px;
    font-size: 34px; font-weight: 400; color: var(--ink); letter-spacing: .5px;
  }
  .brand-name .dot {
    display: inline-block; width: 10px; height: 10px; border-radius: 50%;
    background: var(--rose-red); margin-left: 8px; vertical-align: middle;
  }
  .brand-rule { width: 190px; height: 1px; background: var(--ink); opacity: .5; margin: 8px auto 0; }
  .person-name { margin-top: 34px; font-size: 34px; font-weight: 500; }
  .person-role { font-size: 16px; margin-top: 2px; }
  .contact { margin-top: 62px; font-size: 17px; line-height: 1.45; }

  /* back */
  .couple-photo {
    position: absolute; left: 0; top: 60px; width: 100%; height: 265px;
    background: linear-gradient(90deg, #f4f2e6 0%, #e8e6da 30%, #c9a699 55%, #b68a7e 75%, #a7867f 100%);
  }
  .back-brand {
    position: absolute; left: 34px; top: 10px;
    font-size: 34px; line-height: 40px; font-weight: 400; color: var(--white); letter-spacing: .5px;
  }
  .back-brand .dot {
    display: inline-block; width: 10px; height: 10px; border-radius: 50%;
    border: 1.5px solid var(--white); margin-left: 8px; vertical-align: middle;
  }
  .back-band {
    position: absolute; left: 0; bottom: 0; width: 100%; height: 64px;
    background: var(--slate-deep);
    display: flex; align-items: center; justify-content: flex-end; padding-right: 28px;
  }
  .email { color: var(--white); font-size: 22px; letter-spacing: .3px; }
</style>
</head>
<body>
  <section class="card card--front">
    <div class="bouquet-photo" role="img" aria-label="Bridal bouquet of red roses and white lilies"></div>
    <p class="tagline">Making every celebration glow with wonder...</p>
    <div class="front-info">
      <p class="brand-name">Velvet Lantern<span class="dot"></span></p>
      <div class="brand-rule"></div>
      <h1 class="person-name">Rosalind Merrow</h1>
      <p class="person-role">Event Manager</p>
      <p class="contact">www.velvetlanternco.com.au<br>0491 868 254</p>
    </div>
  </section>

  <section class="card card--back">
    <div class="couple-photo" role="img" aria-label="White calla lily bouquet beside a couple's hands wearing wedding rings"></div>
    <p class="back-brand">Velvet Lantern<span class="dot"></span></p>
    <div class="back-band">
      <p class="email">rosalind@velvetlanternco.com.au</p>
    </div>
  </section>
</body>
</html>
```